postcard design for a design company to promote itself in a new area

I am putting out postcards to hairdressing salons that I have renovated recently to target there client base and to offer a discount to the initial consult to there loyal clients. I would like to have a vibrant front design that I can change every twelve weeks with my logo (existing) imbedding into a vibrate, energetic, stylish yet creative front. I want something very colourful fun and inviting that makes people want to pick it up, it should contain some style of pattern and I don't want it all to be my logo. My existing logo I would like on the front but only small or built into the pattern it can be in a different colour and the out side shape can change as long its still the same letters etc.. The pattern can contain words.. The following is what I have written that will be on the back of the post card so you can understand the feel of it.

Brielle from Larkmoor Interiors is partnering up with Marisol and Delphine from Kilo Lock
As we have something special in common, we both want our clients to look & feel fabulous
Brielle is offering the loyal clients of Kilo Lock a special in home consult at a reduced rate.
What we do: Create innovative yet practical design solutions, window treatments & furniture, which are stylish, happy & memorable. Design to us is about you, who you are & how you live, we are passionate about creating a space that is for you and about you.
A well-designed space makes you feel 10 years younger and truly fabulous to be in, it does not have to cost the earth, but it is something everyone should go home to…
Call today to find out how we can add value & create a space that makes you feel wonderful to be in.
m 0491 352 786

Any suggestions on the wording would be appreciated... Especially the 'A well designed space makes you feel 10years younger'

I have attached my existing logo the colour can change.

I want to reach out to the people sitting in the chair getting there hair done and make them want to know a little more about my business. I would like the post card to feel fresh young new and happy.

```html
<!DOCTYPE html>
<html lang="en">
<head>
<meta charset="utf-8">
<title>Larkmoor Interiors Postcard</title>
<link rel="stylesheet" href="https://fonts.googleapis.com/css2?family=Arimo:wght@400;700&family=Kalam:wght@400;700&display=swap">
<style>
  :root {
    --page: #ffffff;
    --card-dark: #2b2b2b;
    --card-mid: #4a4a4a;
    --cyan: #1ee3f2;
    --ink: #1d1d1d;
    --white: #ffffff;
    --panel: #ffffff;
  }
  * { box-sizing: border-box; margin: 0; padding: 0; }
  html, body { width: 1200px; height: 1150px; overflow: hidden; background: var(--page); }
  .canvas { position: relative; width: 1200px; height: 1150px; }

  .postcard {
    position: absolute; left: 70px; width: 1060px; height: 498px;
    overflow: hidden;
  }
  .postcard--front { top: 66px; }
  .postcard--back { top: 584px; }

  .swirl-pattern {
    position: absolute; inset: 0;
    background: radial-gradient(ellipse at 30% 40%, var(--card-mid) 0%, var(--card-dark) 60%),
                var(--card-dark);
  }

  .photo {
    position: absolute;
    box-shadow: 4px 6px 12px rgba(0,0,0,0.6);
  }
  .photo--table { left: 0; top: 61px; width: 228px; height: 292px;
    background: linear-gradient(135deg, #b8d23a 0%, #c9c3a2 50%, #7a6f52 100%); }
  .photo--bedroom { left: 247px; top: 124px; width: 277px; height: 185px;
    background: linear-gradient(160deg, #e9eef0 0%, #f1b58c 55%, #d98b62 100%); }
  .photo--dresser { left: 546px; top: 74px; width: 218px; height: 273px;
    background: linear-gradient(180deg, #eaeae2 0%, #2f86b8 30%, #5b1a1a 60%, #4a1414 100%); }
  .photo--plants { left: 815px; top: 74px; width: 245px; height: 175px;
    background: linear-gradient(120deg, #1f3b30 0%, #4f7a3a 45%, #e8e4da 75%, #a26c3f 100%); }

  .brand-tile {
    position: absolute; background: var(--cyan);
    width: 176px; height: 184px;
    display: flex; align-items: flex-end; justify-content: center;
    padding-bottom: 14px;
  }
  .brand-tile__name {
    font-family: "Arimo", Arial, sans-serif; font-weight: 400;
    font-size: 12px; letter-spacing: 1.5px; text-transform: uppercase;
    color: var(--white);
  }
  .postcard--front .brand-tile { left: 847px; top: 288px; }
  .postcard--back .brand-tile { left: 843px; top: 279px; box-shadow: 4px 6px 12px rgba(0,0,0,0.35); }

  .tagline {
    position: absolute; left: 120px; top: 388px; width: 550px;
    text-align: center; color: var(--white);
    font-family: "Kalam", cursive; font-weight: 700;
    font-size: 28px; line-height: 36px;
    text-shadow: 2px 3px 3px rgba(0,0,0,0.8);
  }

  .info-panel {
    position: absolute; left: 79px; top: 69px; width: 973px; height: 360px;
    background: var(--panel);
    box-shadow: 3px 5px 10px rgba(0,0,0,0.5);
  }
  .photo--round {
    left: 35px; top: 37px; width: 230px; height: 230px; border-radius: 50%;
    border: 3px solid var(--white);
    background: radial-gradient(circle at 50% 35%, #3f7a3a 0%, #9fb98a 40%, #f3f3f0 70%, #d9d9d6 100%);
  }

  .intro, .services__title, .services__text {
    position: absolute; left: 90px; width: 860px;
    text-align: center; color: var(--ink);
    font-family: "Arimo", Arial, sans-serif; font-size: 16.5px; line-height: 21.5px;
  }
  .intro { top: 22px; left: 100px; }
  .services__title {
    top: 120px; color: var(--cyan); font-weight: 700; font-size: 21px; line-height: 26px;
  }
  .services__text { top: 146px; }
  .promise {
    position: absolute; left: 38px; top: 214px; width: 720px;
    font-family: "Arimo", Arial, sans-serif; font-size: 16.5px; line-height: 21.5px;
    color: var(--ink);
  }
  .call-to-action {
    position: absolute; left: 38px; top: 268px; width: 760px;
    font-family: "Kalam", cursive; font-size: 14.5px; line-height: 22px; color: var(--ink);
  }
  .phone {
    position: absolute; left: 38px; top: 307px;
    font-family: "Arimo", Arial, sans-serif; font-size: 22px; line-height: 28px;
    color: var(--cyan);
  }
</style>
</head>
<body>
<main class="canvas">

  <section class="postcard postcard--front">
    <div class="swirl-pattern" role="img" aria-label="Dark charcoal background with large grey swirling pattern"></div>
    <div class="photo photo--table" role="img" aria-label="Photo of a dining table set with lilies against a lime green wall"></div>
    <div class="photo photo--bedroom" role="img" aria-label="Photo of a bright bedroom with a peach patterned bedspread by a window"></div>
    <div class="photo photo--dresser" role="img" aria-label="Photo of a dark wooden dresser with plants in vases and a blue artwork"></div>
    <div class="photo photo--plants" role="img" aria-label="Photo of plants in glass vases against a dark green wall"></div>
    <p class="tagline">We can add value &amp; create a space<br>that makes you feel wonderful to be in.</p>
    <div class="brand-tile"><span class="brand-tile__name">Larkmoor Interiors</span></div>
  </section>

  <section class="postcard postcard--back">
    <div class="swirl-pattern" role="img" aria-label="Dark charcoal background with large grey swirling pattern"></div>
    <div class="info-panel">
      <p class="intro">Brielle from Larkmoor Interiors is partnering up with Marisol and Delphine<br>from Kilo Lock As we have something special in common, we both want our<br>clients to look &amp; feel fabulous Brielle is offering the loyal clients of Kilo Lock a<br>special in home consult at a reduced rate.</p>
      <h2 class="services__title">WHAT WE DO</h2>
      <p class="services__text">Create innovative yet practical design solutions, window treatments &amp; furniture, which<br>are stylish, happy &amp; memorable. Design to us is about you, who you are &amp; how you live, we<br>are passionate about creating a space that is for you and about you.</p>
      <p class="promise">A well-designed space makes you feel 10 years younger and truly fabulous to be in,<br>it does not have to cost the earth, but it is something everyone should go home to…</p>
      <p class="call-to-action">Call today to find out how we can add value &amp; create a space that makes you feel wonderful to be in.</p>
      <p class="phone">M 0491 352 786</p>
    </div>
    <div class="photo photo--round" role="img" aria-label="Round photo of a white sideboard with green potted plants"></div>
    <div class="brand-tile"><span class="brand-tile__name">Larkmoor Interiors</span></div>
  </section>

</main>
</body>
</html>
```